Maple Roster Business Card for recruitment company

We are looking for a Business Card Design that incorporates our personal details and our busines name and logo. We are a specialized search consultancy that recruit Property and Construction professionals.
We would like a business card that stands out and is appealing to the Construction and Property industry as well.

Target Market(s)

people in the construction and property industry

Contact Information for Business Card

Business Name and logo

Font styles to use
Serif

Colors
0094D4
00A9DD
6FCCEA
C7EBF8
E9F6FB

Requirements
Must have
• Business name and logo as well as contact details
Should not have
• No photos of us please

```html
<!DOCTYPE html>
<html lang="en">
<head>
<meta charset="utf-8">
<title>Maple Roster Business Card</title>
<link href="https://fonts.googleapis.com/css2?family=Arimo:wght@400;700&display=swap" rel="stylesheet">
<style>
  :root {
    --teal: #023c50;
    --needle-tone: #0a4a60;
    --paper: #ffffff;
    --backdrop-light: #c9c9c9;
    --backdrop-dark: #a9a9a9;
  }
  * { margin: 0; padding: 0; box-sizing: border-box; }
  html, body { width: 1200px; height: 1015px; overflow: hidden; }
  body {
    position: relative;
    background: radial-gradient(ellipse at 50% 55%, var(--backdrop-light), var(--backdrop-dark));
    font-family: "Arimo", Arial, sans-serif;
  }
  .card {
    position: absolute;
    width: 600px;
    height: 343px;
    overflow: hidden;
    box-shadow: 0 10px 24px rgba(0,0,0,0.35);
  }
  .card-front {
    left: 90px; top: 120px;
    background: var(--teal);
    display: flex; align-items: center; justify-content: center;
  }
  .wordmark {
    font-weight: 400;
    text-transform: uppercase;
    letter-spacing: 0.08em;
    font-size: 40px;
  }
  .card-front .wordmark { color: var(--paper); }
  .card-back { left: 510px; top: 545px; background: var(--paper); }
  .back-art { position: absolute; inset: 0; }
  .card-back .wordmark {
    position: absolute; left: 36px; top: 118px;
    color: var(--teal); font-size: 30px;
  }
  .contact {
    position: absolute; right: 26px; top: 112px;
    color: var(--paper); text-align: right;
    font-size: 13px; line-height: 1.35;
  }
  .contact .person-name { font-size: 17px; font-weight: 700; letter-spacing: 0.04em; text-transform: uppercase; }
  .contact .person-role { font-size: 11px; letter-spacing: 0.06em; text-transform: uppercase; margin-bottom: 10px; }
  .contact-line { display: flex; justify-content: flex-end; align-items: center; gap: 6px; }
  .contact-line svg { width: 12px; height: 12px; flex: none; }
  .address { margin-top: 10px; }
</style>
</head>
<body>
  <section class="card card-front">
    <span class="wordmark">Maple Roster</span>
  </section>

  <section class="card card-back">
    <svg class="back-art" viewBox="0 0 600 343" width="600" height="343">
      <polygon points="430,0 600,0 600,343 368,343" fill="var(--teal)"/>
      <polygon class="needle-area" role="img" aria-label="Illustration of a sewing needle"
               points="384,28 414,28 378,343 362,343"
               fill="var(--needle-tone)" stroke="var(--paper)" stroke-width="3"/>
    </svg>

    <span class="wordmark">Maple Roster</span>

    <div class="contact">
      <div class="person-name">Daniel Hart</div>
      <div class="person-role">Managing Director</div>
      <div class="contact-line">044-987 654 321
        <svg viewBox="0 0 12 12"><path d="M2.5 1 L4.5 1 L5 3.5 L3.8 4.5 Q5 7 7.5 8.2 L8.5 7 L11 7.5 L11 9.5 Q11 11 9.5 11 Q1 10 1 2.5 Q1 1 2.5 1 Z" fill="var(--paper)"/></svg>
      </div>
      <div class="contact-line">info@mapleroster.com
        <svg viewBox="0 0 12 12"><rect x="0.5" y="2.5" width="11" height="7.5" fill="var(--paper)"/><path d="M0.5 2.5 L6 7 L11.5 2.5" fill="none" stroke="var(--teal)" stroke-width="1"/></svg>
      </div>
      <div class="contact-line">www.mapleroster.com
        <svg viewBox="0 0 12 12"><circle cx="6" cy="6" r="5.2" fill="none" stroke="var(--paper)" stroke-width="1.2"/><ellipse cx="6" cy="6" rx="2.3" ry="5.2" fill="none" stroke="var(--paper)" stroke-width="1"/><path d="M1 6 H11 M2 3.5 H10 M2 8.5 H10" stroke="var(--paper)" stroke-width="0.9"/></svg>
      </div>
      <div class="address">18, Harbour Street West<br>30517, Northland</div>
    </div>
  </section>
</body>
</html>
```